The Copper Kite Website Redesign

I want a new design and website for www.thecopperkitebrookvale.com where part of the home page includes our daily specials from our POS Toast to be pulled from API. I have included photos and links to give you a better feel for the style of our restaurant.

Coding

Coded - Design and coding required

```html
<!DOCTYPE html>
<html lang="en">
<head>
<meta charset="utf-8">
<title>The Copper Kite – a finer diner</title>
<link rel="stylesheet" href="https://fonts.googleapis.com/css2?family=Sedgwick+Ave+Display&family=Dancing+Script:wght@500;700&family=Poppins:wght@400;500&display=swap">
<style>
:root{
  --ink:#231f20;
  --white:#ffffff;
  --paper:#efeded;
  --text:#3a3a3a;
}
*{box-sizing:border-box;margin:0;padding:0}
html,body{width:1200px;height:4710px;overflow:hidden}
body{position:relative;background:var(--white);font-family:"Poppins",sans-serif;color:var(--text)}
.abs{position:absolute}
.display{font-family:"Sedgwick Ave Display",cursive;color:var(--ink);font-weight:400;white-space:nowrap}
.script{font-family:"Dancing Script",cursive;color:var(--ink);white-space:nowrap}
.btn{position:absolute;background:var(--ink);color:var(--white);border-radius:6px;display:flex;align-items:center;justify-content:center;font-family:"Poppins",sans-serif}
.photo{position:absolute}

/* header */
.site-header{position:absolute;left:0;top:0;width:1200px;height:137px}
.brand{position:absolute;left:68px;top:30px;color:var(--white);font-family:"Sedgwick Ave Display",cursive;font-size:52px;line-height:1;white-space:nowrap}
.brand-tag{position:absolute;left:72px;top:90px;color:var(--white);font-size:13px;letter-spacing:1px}
.top-contact{position:absolute;top:24px;display:flex;align-items:center;gap:10px;color:var(--white);font-size:13px;white-space:nowrap}
.top-contact svg{width:26px;height:26px}
.nav{position:absolute;top:90px;left:640px;font-size:14px;color:var(--ink)}
.nav a{color:inherit;text-decoration:none;position:absolute;white-space:nowrap;top:5px}
.nav .current{border-bottom:2px solid var(--ink);padding-bottom:2px}
.nav .cta{background:var(--ink);color:var(--white);top:0;width:108px;height:29px;display:flex;align-items:center;justify-content:center;font-size:13px}

/* hero */
.hero{position:absolute;left:0;top:137px;width:1200px;height:521px}
.hero h1{position:absolute;left:150px;top:70px;font-size:132px;line-height:1}
.hero .sub-title{position:absolute;left:155px;top:208px;font-size:96px;line-height:1;font-weight:700}
.hero p{position:absolute;left:158px;top:340px;font-size:17px;color:var(--ink);white-space:nowrap}

/* general info */
.info{position:absolute;left:0;top:658px;width:1200px;height:535px;background:linear-gradient(120deg,#f6ecea,#f3eeec 40%,#f5e8e6 70%,#f1ecea)}
.info h2{position:absolute;left:0;width:1200px;text-align:center;top:55px;font-size:96px;line-height:1}
.fact{position:absolute;width:400px}
.fact .icon{position:absolute;left:-106px;top:4px;width:80px;height:80px}
.fact h3{font-size:27px;font-weight:500;color:var(--ink);line-height:1.2}
.fact p{font-size:19px;line-height:1.2;color:var(--ink);margin-top:4px}

/* about */
.about{position:absolute;left:0;top:1193px;width:1200px;height:521px;background:var(--paper)}
.about h2{position:absolute;left:633px;top:72px;font-size:80px;line-height:1}
.about p{position:absolute;left:633px;top:186px;width:434px;font-size:13.5px;line-height:26.8px;text-align:justify;color:#555}

/* menu */
.menu{position:absolute;left:0;top:1714px;width:1200px;height:764px}
.menu h2{position:absolute;left:0;width:1200px;text-align:center;top:62px;font-size:72px;line-height:1}
.menu .lede{position:absolute;left:0;width:1200px;text-align:center;top:152px;font-size:26px}
.tab{position:absolute;top:230px;width:183px;height:50px;border:1.5px solid var(--ink);border-radius:7px;display:flex;align-items:center;justify-content:center;font-family:"Sedgwick Ave Display",cursive;font-size:23px;color:var(--ink);white-space:nowrap}
.tab.active{background:var(--ink);color:var(--white)}
.arrow{position:absolute;top:421px;width:40px;height:40px;border-radius:50%;background:#b8b8b8}
.dish{position:absolute;top:325px;width:282px;text-align:center}
.dish .photo{position:relative;width:282px;height:207px;border-radius:12px}
.dish h3{font-family:"Sedgwick Ave Display",cursive;font-weight:400;font-size:27px;color:var(--ink);margin-top:22px;line-height:1.2;white-space:nowrap}
.dish p{font-size:14.5px;line-height:18px;color:var(--ink);margin:10px auto 0;width:260px}
.price{display:inline-block;margin-top:14px;background:var(--ink);color:var(--white);font-size:16px;width:102px;height:28px;line-height:28px}

/* price lists */
.drinks{position:absolute;left:0;top:2478px;width:1200px;height:558px;background:var(--paper)}
.sides{position:absolute;left:0;top:3036px;width:1200px;height:564px}
.label-bar{position:absolute;left:0;bottom:0;width:100%;height:66px;background:var(--ink);color:var(--white);font-family:"Sedgwick Ave Display",cursive;font-size:44px;display:flex;align-items:center;justify-content:center;white-space:nowrap}
.price-list{position:absolute;list-style:none;font-size:14.2px;color:var(--ink)}
.price-list li{display:flex;align-items:baseline;height:26.7px}
.price-list .item{white-space:nowrap}
.price-list .leader{flex:1;border-bottom:1.5px dotted #777;margin:0 4px;transform:translateY(-4px)}
.price-list .cost{white-space:nowrap}

/* contact */
.contact{position:absolute;left:0;top:3600px;width:1200px;height:634px}
.contact h2{position:absolute;left:0;width:1200px;text-align:center;top:62px;font-size:80px;line-height:1}
.contact .lede{position:absolute;left:0;width:1200px;text-align:center;top:188px;font-size:22px}
.field{position:absolute;border:1.5px solid #e2e2e2;background:var(--white);color:#b5b5b5;font-size:14px;padding:14px 12px}

/* footer */
.site-footer{position:absolute;left:0;top:4234px;width:1200px;height:476px;background:var(--ink);color:var(--white)}
.site-footer h4{position:absolute;font-family:"Sedgwick Ave Display",cursive;font-weight:400;font-size:24px;letter-spacing:1px;white-space:nowrap}
.foot-brand{position:absolute;left:91px;top:136px;font-family:"Sedgwick Ave Display",cursive;font-size:44px;line-height:1;white-space:nowrap}
.social{position:absolute;top:236px;width:34px;height:34px;border-radius:50%;background:var(--white)}
.foot-links{position:absolute;left:353px;top:152px;list-style:none;font-size:18px;line-height:32.4px}
.foot-links li::before{content:"";display:inline-block;width:7px;height:7px;border-radius:50%;background:var(--white);margin-right:16px;vertical-align:middle}
.foot-contact{position:absolute;left:608px;font-size:17px;line-height:25px;white-space:nowrap}
.foot-icon{position:absolute;left:560px;width:38px;height:38px}
.newsletter p{position:absolute;left:860px;top:150px;width:290px;font-size:17px;line-height:28px}
.rule{position:absolute;left:71px;top:396px;width:1067px;height:1px;background:#777}
.copyright{position:absolute;left:0;width:1200px;text-align:center;top:428px;font-size:14px}
</style>
</head>
<body>

<header class="site-header">
  <svg class="abs" width="1200" height="137" viewBox="0 0 1200 137" aria-hidden="true">
    <rect x="0" y="0" width="1200" height="68" fill="var(--ink)"/>
    <polygon points="0,0 448,0 448,68 411,137 0,137" fill="var(--ink)"/>
  </svg>
  <div class="brand">The Copper Kite</div>
  <div class="brand-tag">a finer diner</div>
  <div class="top-contact" style="left:690px">
    <svg viewBox="0 0 26 26"><rect x="1" y="1" width="24" height="24" rx="4" fill="none" stroke="#fff" stroke-width="1.6"/><rect x="6" y="8" width="14" height="10" fill="#fff"/><path d="M6 8 L13 14 L20 8" fill="none" stroke="#231f20" stroke-width="1.4"/></svg>
    <span>eat@thecopperkitebrookvale.com</span>
  </div>
  <div class="top-contact" style="left:985px">
    <svg viewBox="0 0 26 26"><rect x="1" y="1" width="24" height="24" rx="4" fill="none" stroke="#fff" stroke-width="1.6"/><path d="M8 6 L11 6 L12 10 L10 11.5 Q12 15 14.5 16 L16 14 L20 15 L20 18 Q18 20 15 19 Q9 17 7 10 Q6.5 7 8 6Z" fill="#fff"/></svg>
    <span>+1 555 014 2260</span>
  </div>
  <nav class="nav">
    <a class="current" style="left:13px">Home</a>
    <a style="left:84px">About Us</a>
    <a style="left:181px">Menu</a>
    <a style="left:253px">Retail</a>
    <a style="left:324px">Press</a>
    <a class="cta" style="left:382px">Contact US</a>
  </nav>
</header>

<section class="hero">
  <h1 class="display">Delicious</h1>
  <div class="sub-title script">Food Menu</div>
  <p>We Offer fresh and Quality Service to Our guests</p>
  <a class="btn" style="left:247px;top:392px;width:229px;height:58px;font-size:20px">Book A Table Now</a>
  <div class="photo" role="img" aria-label="Waffle topped with whipped cream, blueberries and strawberries" style="left:655px;top:0;width:545px;height:521px;background:radial-gradient(circle at 55% 40%,#f4f1f3 0 18%,#c7893f 30%,#9a5a2a 55%,#d9d6d8 80%,#eceaeb)"></div>
</section>

<section class="info">
  <h2 class="display">General Informtion</h2>
  <div class="fact" style="left:199px;top:212px">
    <svg class="icon" viewBox="0 0 80 80" aria-hidden="true"><circle cx="40" cy="40" r="38" fill="#fff" stroke="var(--ink)" stroke-width="2.5"/><circle cx="40" cy="40" r="26" fill="none" stroke="var(--ink)" stroke-width="2.5"/><path d="M40 24 V40 L50 47" stroke="var(--ink)" stroke-width="3" fill="none" stroke-linecap="round"/></svg>
    <h3>Hours:</h3>
    <p>Saturday through Sunday-8am- until 8 p.m. Please call for any holiday hour's information.</p>
  </div>
  <div class="fact" style="left:724px;top:212px">
    <svg class="icon" viewBox="0 0 80 80" aria-hidden="true"><circle cx="40" cy="40" r="38" fill="#fff" stroke="var(--ink)" stroke-width="2.5"/><path d="M26 24 H38 L36 42 Q32 46 28 42Z M42 24 H54 L52 42 Q48 46 44 42Z M32 45 V58 M48 45 V58 M27 58 H37 M43 58 H53" stroke="var(--ink)" stroke-width="2.5" fill="none" stroke-linecap="round"/></svg>
    <h3>Booze:</h3>
    <p>we have a full bar! Beer, Wine and Booze… Catch a Buzzill</p>
  </div>
  <div class="fact" style="left:199px;top:344px">
    <svg class="icon" viewBox="0 0 80 80" aria-hidden="true"><circle cx="40" cy="40" r="38" fill="#fff" stroke="var(--ink)" stroke-width="2.5"/><circle cx="42" cy="42" r="12" fill="none" stroke="var(--ink)" stroke-width="2.5"/><path d="M20 24 V36 Q20 40 23 40 V60 M26 24 V36 Q26 40 23 40 M60 24 Q54 32 56 44 H60 V60" stroke="var(--ink)" stroke-width="2.5" fill="none" stroke-linecap="round"/></svg>
    <h3>Blunch:</h3>
    <p>It is what we call our menu, and ALL items are available ALL hours we are open!</p>
  </div>
  <div class="fact" style="left:724px;top:344px">
    <svg class="icon" viewBox="0 0 80 80" aria-hidden="true"><circle cx="40" cy="40" r="38" fill="#fff" stroke="var(--ink)" stroke-width="2.5"/><rect x="22" y="32" width="32" height="20" rx="3" transform="rotate(-20 38 42)" fill="#fff" stroke="var(--ink)" stroke-width="2.5"/><rect x="28" y="38" width="32" height="20" rx="3" fill="#fff" stroke="var(--ink)" stroke-width="2.5"/><path d="M28 44 H60" stroke="var(--ink)" stroke-width="4"/></svg>
    <h3>Plastic:</h3>
    <p>we gladly accept all major credit cards!</p>
  </div>
</section>

<section class="about">
  <div class="photo" role="img" aria-label="Waffles with syrup on a diner counter" style="left:168px;top:84px;width:399px;height:360px;background:linear-gradient(160deg,#5a3a30,#a8552e 35%,#2c2524 55%,#b57a3f 75%,#3b2d28)"></div>
  <h2 class="display">About Us</h2>
  <p>The doors of The Copper Kite: a finer diner were eagerly thrown open for the first time on December 28th 2004. We welcomed our first customers and started our magnificent life as a business that continues on through today. Along with our beloved and inquisitive customers came the many questions of our origin. The most important of which we will address right here and now…</p>
  <a class="btn" style="left:635px;top:404px;width:157px;height:46px;font-size:14px">Discover More</a>
</section>

<section class="menu">
  <h2 class="display">Our Menu</h2>
  <div class="lede script">We cook our dishes from the freshest ingredients</div>
  <div class="tab active" style="left:126px">All Things Eggs</div>
  <div class="tab" style="left:318px">Oh, Sugar Shack</div>
  <div class="tab" style="left:510px">Green Things</div>
  <div class="tab" style="left:702px">Between Bread</div>
  <div class="tab" style="left:894px">Other Stuff</div>
  <svg class="arrow" style="left:68px" viewBox="0 0 40 40" aria-hidden="true"><path d="M23 13 L16 20 L23 27" stroke="#fff" stroke-width="2.5" fill="none"/></svg>
  <svg class="arrow" style="left:1090px" viewBox="0 0 40 40" aria-hidden="true"><path d="M17 13 L24 20 L17 27" stroke="#fff" stroke-width="2.5" fill="none"/></svg>
  <article class="dish" style="left:139px">
    <div class="photo" role="img" aria-label="Green eggs and ham on a lime green plate" style="background:radial-gradient(circle at 55% 50%,#f3c23a 0 10%,#fff 14%,#b7d63a 30%,#e8e4de 60%)"></div>
    <h3>Green Eggs and Ham</h3>
    <p>Poblano Pesto and Jack Cheese Rumbled with Eggs Sidled by Seared City Ham.</p>
    <span class="price">$13.95</span>
  </article>
  <article class="dish" style="left:459px">
    <div class="photo" role="img" aria-label="Veggie rumble on a white plate with lettuce" style="background:radial-gradient(circle at 50% 55%,#7d6a3e 0 18%,#f4f2ee 32%,#6e8a3a 45%,#4a3c34 70%)"></div>
    <h3>Veggie Rumble</h3>
    <p>Red Pepper, Carrots, Mushrooms, Peas, Spinach and Provolone. Choose Eggs or Tofu</p>
    <span class="price">$12.95</span>
  </article>
  <article class="dish" style="left:777px">
    <div class="photo" role="img" aria-label="Red flannel hash in a red bowl" style="background:radial-gradient(circle at 50% 50%,#a8301f 0 25%,#c7423a 45%,#2e3a5a 75%)"></div>
    <h3>Red Flannel Hash</h3>
    <p>Hot Spiced Beef Brisket, Potatoes, Beets &amp; Onion with Two Eggs and Scallions</p>
    <span class="price">$13.95</span>
  </article>
</section>

<section class="drinks">
  <div class="photo" role="img" aria-label="Cup of tea on a porcelain saucer" style="left:112px;top:83px;width:426px;height:397px;background:radial-gradient(circle at 40% 45%,#8c3a22 0 10%,#e7e6f0 22%,#8a7a6a 50%,#3e3430)">
    <div class="label-bar">Other Whistle Wetters</div>
  </div>
  <ul class="price-list" style="left:605px;top:102px;width:509px">
    <li><span class="item">Hollow Oak Roasters 'Ritual' Blend</span><span class="leader"></span><span class="cost">$2.95</span></li>
    <li><span class="item">Whitcombe &amp; Daughters Loose Leaf Tea</span><span class="leader"></span><span class="cost">$3.95</span></li>
    <li><span class="item">Fresh Squeezed O.J.</span><span class="leader" style="margin-left:160px"></span><span class="cost">sm.$3.95 lg.$4.95</span></li>
    <li><span class="item">Fresh Squeezed Lemonades</span><span class="leader"></span><span class="cost">$3.95</span></li>
    <li><span class="item">Hot Cocoa with Whipped Cream</span><span class="leader"></span><span class="cost">$2.95</span></li>
    <li><span class="item">Lil' Can o' Veggie Juice</span><span class="leader"></span><span class="cost">$2.50</span></li>
    <li><span class="item">Bottled Root Beer</span><span class="leader"></span><span class="cost">$2.95</span></li>
    <li><span class="item">Fountain Drinks</span><span class="leader"></span><span class="cost">$2.50</span></li>
    <li><span class="item">Kumo Iced Green Tea</span><span class="leader"></span><span class="cost">$3.50</span></li>
    <li><span class="item">Fresh-Brewed Iced Tea</span><span class="leader"></span><span class="cost">$2.50</span></li>
    <li><span class="item">Fairway Classic a.k.a. Half and Half</span><span class="leader"></span><span class="cost">$2.50</span></li>
    <li><span class="item">Rootbeer Float</span><span class="leader"></span><span class="cost">$5.95</span></li>
    <li><span class="item">Grapefruit Juice</span><span class="leader" style="margin-left:190px"></span><span class="cost">sm.$1.95 lg.$2.95</span></li>
  </ul>
</section>

<section class="sides">
  <ul class="price-list" style="left:99px;top:104px;width:510px">
    <li><span class="item">Daily Soup</span><span class="leader" style="margin-left:170px"></span><span class="cost">cup $5.00/bowl $6.00</span></li>
    <li><span class="item">Black Beans</span><span class="leader" style="margin-left:170px"></span><span class="cost">$5.00</span></li>
    <li><span class="item">Seared Shrimp.</span><span class="leader" style="margin-left:150px"></span><span class="cost">$7.00</span></li>
    <li><span class="item">Tempeh Patty</span><span class="leader" style="margin-left:160px"></span><span class="cost">$6.00</span></li>
    <li><span class="item">Tofu</span><span class="leader" style="margin-left:220px"></span><span class="cost">$5.00</span></li>
    <li><span class="item">Pepper Bacon</span><span class="leader" style="margin-left:160px"></span><span class="cost">$6.00</span></li>
    <li><span class="item">Hot Italian Sausage</span><span class="leader" style="margin-left:120px"></span><span class="cost">$6.00</span></li>
    <li><span class="item">Detroit Breakfast Links</span><span class="leader" style="margin-left:95px"></span><span class="cost">$6.00</span></li>
    <li><span class="item">Grilled City Ham</span><span class="leader" style="margin-left:140px"></span><span class="cost">$6.00</span></li>
    <li><span class="item">Chicken Thigh</span><span class="leader" style="margin-left:155px"></span><span class="cost">$6.00</span></li>
    <li><span class="item">House Spuds</span><span class="leader" style="margin-left:165px"></span><span class="cost">$3.95</span></li>
    <li><span class="item">Fries</span><span class="leader" style="margin-left:215px"></span><span class="cost">$3.95</span></li>
    <li><span class="item">Side Salad</span><span class="leader" style="margin-left:180px"></span><span class="cost">$3.95</span></li>
    <li><span class="item">Toast-Sourdough, Multigrain or Rye</span><span class="leader"></span><span class="cost">$3.95</span></li>
  </ul>
  <div class="photo" role="img" aria-label="Seared shrimp with diced peppers" style="left:658px;top:84px;width:427px;height:395px;background:radial-gradient(circle at 45% 40%,#e6a28a 0 15%,#c8553f 35%,#7a2a22 60%,#3a2422)">
    <div class="label-bar">B-Sides</div>
  </div>
</section>

<section class="contact">
  <h2 class="display">Contact Us</h2>
  <div class="lede script">For more information,Please fill out the following and we will be in touch shortly</div>
  <div class="photo" role="img" aria-label="Burger with sesame bun on a dark background" style="left:135px;top:259px;width:417px;height:307px;background:radial-gradient(ellipse at 50% 50%,#c07a35 0 18%,#8a2a1e 28%,#5a3a1e 38%,#1a1614 62%)"></div>
  <div class="field" style="left:615px;top:259px;width:215px;height:49px">First Name</div>
  <div class="field" style="left:854px;top:259px;width:216px;height:49px">Second Name</div>
  <div class="field" style="left:615px;top:338px;width:215px;height:49px">Phone</div>
  <div class="field" style="left:854px;top:338px;width:216px;height:49px">Subject</div>
  <div class="field" style="left:615px;top:411px;width:459px;height:101px">Message</div>
  <a class="btn" style="left:615px;top:534px;width:80px;height:30px;font-size:14px;border-radius:2px">Submit</a>
</section>

<footer class="site-footer">
  <div class="foot-brand">The Copper Kite</div>
  <div class="social" style="left:113px"></div>
  <div class="social" style="left:160px"></div>
  <div class="social" style="left:208px"></div>

  <h4 style="left:353px;top:80px">LINKS</h4>
  <ul class="foot-links">
    <li>About Us</li><li>Menu</li><li>Retail</li><li>Press</li><li>Contact us</li>
  </ul>

  <h4 style="left:560px;top:80px">CONTACT US</h4>
  <svg class="foot-icon" style="top:160px" viewBox="0 0 38 38" aria-hidden="true"><circle cx="19" cy="19" r="19" fill="#fff"/><path d="M19 8 Q12 8 12 15 Q12 21 19 30 Q26 21 26 15 Q26 8 19 8Z" fill="var(--ink)"/><circle cx="19" cy="15" r="3" fill="#fff"/></svg>
  <div class="foot-contact" style="top:157px">ADDRESS:<br>4180 Larkspur Ave.<br>Brookvale, MI 48031.</div>
  <svg class="foot-icon" style="top:252px" viewBox="0 0 38 38" aria-hidden="true"><circle cx="19" cy="19" r="19" fill="#fff"/><path d="M12 10 L16 10 L17.5 15 L15 16.5 Q17 21 21 23 L23 20.5 L28 22 L28 26 Q25 29 21 27.5 Q13 24 10.5 15 Q10 11.5 12 10Z" fill="var(--ink)"/></svg>
  <div class="foot-contact" style="top:249px">PHONE:<br>+1 555 014 2260</div>
  <svg class="foot-icon" style="top:323px" viewBox="0 0 38 38" aria-hidden="true"><circle cx="19" cy="19" r="19" fill="#fff"/><rect x="10" y="12" width="18" height="13" fill="var(--ink)"/><path d="M10 12 L19 19 L28 12" fill="none" stroke="#fff" stroke-width="1.5"/></svg>
  <div class="foot-contact" style="top:320px">EMAIL:<br>eat@thecopperkitebrookvale.com</div>

  <div class="newsletter">
    <h4 style="left:860px;top:80px">NEWSLETTER SIGN UP</h4>
    <p>To stay up to date on all the latest news from us</p>
    <div class="field" style="left:861px;top:218px;width:271px;height:45px;border-radius:8px;padding:11px 20px">Email</div>
    <div class="abs" style="left:861px;top:284px;width:136px;height:36px;background:#fff;color:var(--ink);font-size:15px;display:flex;align-items:center;justify-content:center">Subscribe</div>
  </div>

  <div class="rule"></div>
  <div class="copyright">© 2011 the copper kite . All Rights Reserved.</div>
</footer>

</body>
</html>
```